whitening syringe artwork design

3ml syringe with silkscreen printing:
sample:
https://www.quorvashop.example/Velvo-Crane-Whitening-Syringes-Carbamide/dp/Q51842KX93/ref=sr_1_6?crid=7ZP42WQ81LMRT&dchild=1&keywords=whitening+syringes&qid=1698802214&sprefix=whitening+sy%2Caps%2C150&sr=8-6
inside the writing:
"teeth whitening gel " change to "Orvanne WHITENING GEL"
"Advanced formula" change to our logo and "Not all gels are created equal. "

additional requirements:
Inches: 2.01" wide x 1.34" around

CM: 5.1cm wide x 3.4cm around

See attached template: Generic_Syringe Labels 3ml_Silkscreen.pdf

- Leave the volume gage where it is, so it prints correctly on the syringe

- Feel free to change the color and font style

- An "identifying marker" is required: Teeth Whitening Syringe or Teeth Whitening Gel (for example)

- Replace "Teeth Whitening Gel - Advanced Formula" with your text and logo - it is there as a placeholder

-We require PDF files created to print ready specifications. Color images should be down-sampled to 300DPI

-Please provide us your Tintora color references for the color used in your artwork

https://www.tintora.example/color-finder#/pick?tintoraBook=tintoraSolidCoatedV3M2

-Please ensure that all fonts are embedded in the PDF document or make sure you convert fonts to outlines to prevent any issues with fonts (AI-Type-Create Outlines)

We will need your print ready artwork in a high resolution PDF file

teeth whitening ecommerce

• follow the guide document, and add text I want, color code from Tintora is provided

```html
<!DOCTYPE html>
<html lang="en">
<head>
<meta charset="utf-8">
<title>Whitening Syringe Silkscreen Artwork</title>
<link rel="stylesheet" href="https://fonts.googleapis.com/css2?family=Great+Vibes&family=Montserrat:wght@600&family=Barlow+Condensed:wght@600;700&display=swap">
<style>
  :root {
    --ink-blue: #1f6fb8;
    --ink-navy: #2a2467;
    --ink-grey: #4a4a52;
    --mark-rose: #dba396;
    --paper: #ffffff;
  }
  html, body {
    margin: 0;
    padding: 0;
    overflow: hidden;
    background: var(--paper);
  }
  .artboard {
    position: relative;
    width: 1200px;
    height: 718px;
    overflow: hidden;
    background: var(--paper);
  }

  /* centred placement helper: left/top give the centre point */
  .script-title,
  .brand-name,
  .brand-dot {
    position: absolute;
    transform: translate(-50%, -50%);
  }
  .script-title {
    display: inline-block;
    padding: 0 14px;
    font-family: "Great Vibes", cursive;
    white-space: nowrap;
    line-height: 1.35;
    background: linear-gradient(160deg, var(--ink-blue) 10%, var(--ink-navy) 75%);
    -webkit-background-clip: text;
    background-clip: text;
    color: transparent;
  }
  .brand-name {
    font-family: "Montserrat", sans-serif;
    font-weight: 600;
    color: var(--ink-grey);
    letter-spacing: 0.12em;
    white-space: nowrap;
    line-height: 1;
  }
  .brand-dot {
    border-radius: 50%;
    background: var(--mark-rose);
  }

  .pen-label .script-title { font-size: 56px; }
  .pen-label .brand-name { font-size: 22px; }
  .pen-label .brand-dot { width: 22px; height: 22px; }

  .gel-label .script-title { font-size: 50px; }
  .gel-label .brand-name { font-size: 17px; }
  .gel-label .brand-dot { width: 18px; height: 18px; }

  .tick {
    position: absolute;
    width: 3px;
    background: linear-gradient(180deg, var(--ink-blue), var(--ink-navy));
  }
  .tick--major { top: 424px; height: 62px; }
  .tick--minor { top: 449px; height: 37px; }
  .tick-label,
  .unit-label {
    position: absolute;
    transform: translate(-50%, -50%) rotate(-90deg);
    white-space: nowrap;
    line-height: 1;
    font-family: "Barlow Condensed", sans-serif;
    color: var(--ink-navy);
  }
  .tick-label { font-weight: 700; font-size: 26px; }
  .tick-label--small { font-size: 22px; }
  .unit-label { font-weight: 600; font-size: 19px; }
</style>
</head>
<body>
<main class="artboard">

  <section class="pen-label">
    <span class="script-title" style="left:304px; top:207px">Orvanne Whitening Pen</span>
    <span class="brand-name" style="left:305px; top:248px">MERIDEL</span>
    <span class="brand-dot" style="left:305px; top:277px"></span>
  </section>

  <section class="pen-label">
    <span class="script-title" style="left:310px; top:463px">Orvanne Whitening Pen</span>
    <span class="brand-name" style="left:310px; top:504px">MERIDEL</span>
    <span class="brand-dot" style="left:310px; top:533px"></span>
  </section>

  <section class="gel-label">
    <span class="script-title" style="left:880px; top:292px">Teeth Whitening Gel</span>
    <span class="brand-name" style="left:896px; top:329px">MERIDEL</span>
    <span class="brand-dot" style="left:896px; top:353px"></span>
  </section>

  <section class="volume-gauge" aria-label="Volume gauge in millilitres">
    <span class="tick tick--major" style="left:657px"></span>
    <span class="tick tick--minor" style="left:726px"></span>
    <span class="tick tick--major" style="left:795px"></span>
    <span class="tick tick--minor" style="left:874px"></span>
    <span class="tick tick--major" style="left:953px"></span>
    <span class="tick tick--minor" style="left:1022px"></span>
    <span class="tick tick--major" style="left:1091px"></span>

    <span class="tick-label tick-label--small" style="left:725px; top:419px">½</span>
    <span class="tick-label" style="left:794px; top:408px">1</span>
    <span class="tick-label tick-label--small" style="left:874px; top:422px">1½</span>
    <span class="tick-label" style="left:952px; top:409px">2</span>
    <span class="tick-label tick-label--small" style="left:1022px; top:423px">2½</span>
    <span class="tick-label" style="left:1091px; top:409px">3</span>
    <span class="unit-label" style="left:1107px; top:455px">ml/cc</span>
  </section>

</main>
</body>
</html>
```